QRV Advisors needs a web site

We need a web site for www.qrvadvisors-example.com. QRV is a mergers and acquisition consulting company that focuses our buyer and seller services on logistics companies. We help put companies together, and help with legal and financial due diligence. We want the web site to express our service and show the logistics components. We want personalized images versus pictures of trucks and airplanes.

Our new logo uses Burgandy and grey colors. Image attached. We are not in to bold, big letters...classy, artistic, low key preferred. Confidentiality, experience, professional are what we want to express on the site.

All we expect for the first part of this project is a home page, and one subpage.  We are budgeting other funds for the technical aspects of the web site

Reason: All that I'm seeing so far is trucks, forklifts and planes. We are a legal mergers and acquisitions firm that focus on logistics. I like some of the images to say logistics, but really want it say legal, financial, and putting companies together. Will pay extra for the sub page if someone can impress us with a home page.

Reason: Swamped with another project at the moment...will work on this over the weekend and provide designer feedback and select final design by Tuesday

```html
<!DOCTYPE html>
<html lang="en">
<head>
<meta charset="utf-8">
<title>QRV Advisors — Home</title>
<link href="https://fonts.googleapis.com/css2?family=Ubuntu:ital,wght@0,300;0,400;0,500;1,400&display=swap" rel="stylesheet">
<style>
:root{
  --burgundy:#a0063a;
  --burgundy-dark:#7d022c;
  --grey-text:#444;
  --grey-mid:#666;
  --grey-light:#e9e9e9;
  --panel:#f3f3f3;
  --footer:#0d0d0d;
  --white:#fff;
}
*{box-sizing:border-box;margin:0;padding:0}
html,body{width:1063px;height:1200px;overflow:hidden}
body{position:relative;font-family:"Ubuntu",sans-serif;color:var(--grey-text);
  background:linear-gradient(#fbfbfb 0,#e6e6e6 407px,#fff 407px)}
.abs{position:absolute}
a{color:var(--burgundy)}

.brand{left:141px;top:30px;display:flex;align-items:center;gap:10px;font-size:34px;font-weight:400;color:#5a5a5a;letter-spacing:1px}
.brand-mark{width:22px;height:22px;background:var(--burgundy)}
.call{left:718px;top:43px;font-size:18px;color:#555;display:flex;align-items:center;gap:6px}
.call b{font-weight:500;color:#333}

.nav{left:139px;top:105px;width:782px;height:34px;border-radius:3px;border:2px solid #c9c9c9;
  background:linear-gradient(#b50d46,var(--burgundy-dark));display:flex;align-items:center;justify-content:space-between;padding:0 20px 0 10px}
.nav a{color:var(--white);text-decoration:none;font-size:12px;font-weight:500;letter-spacing:.2px}
.nav a.current{background:var(--white);color:#666;padding:5px 12px;border-radius:2px;font-weight:400}

.hero{left:138px;top:152px;width:785px;height:311px;background:var(--white);border-radius:6px;box-shadow:0 6px 10px rgba(0,0,0,.18)}
.hero-photo{left:3px;top:3px;width:779px;height:306px;border-radius:4px;
  background:linear-gradient(100deg,#c9ccd0 0%,#e7e9ec 35%,#f1f2f4 55%,#b7bcc4 80%,#6e7480 100%)}
.hero-caption{left:3px;top:280px;width:621px;height:29px;background:linear-gradient(90deg,rgba(140,0,45,.92),rgba(160,6,58,.85));
  color:var(--white);font-style:italic;font-size:16px;line-height:29px;padding-left:20px}
.hero-arrows{left:624px;top:280px;width:105px;height:29px;background:var(--white);border-radius:6px 6px 0 0;display:flex}
.hero-arrows span{flex:1;display:flex;align-items:center;justify-content:center;border-right:1px solid #ddd}
.hero-arrows span:last-child{border:0}

.panel{background:linear-gradient(#f0f0f0,#fff 60%);border:1px solid #e2e2e2;border-radius:3px}
.panel h2{font-weight:300;font-size:20px;color:#555}
.panel h2 em{font-style:normal;color:var(--burgundy);font-weight:400}
.rule{height:2px;background:var(--burgundy)}
.welcome{left:139px;top:489px;width:509px;height:188px;padding:8px 12px}
.welcome .rule{width:460px;margin:6px 0 10px}
.welcome p{font-size:10.5px;line-height:15px;letter-spacing:.4px;color:#3e3e3e;margin-bottom:12px}
.more{position:absolute;right:20px;bottom:6px;font-size:10.5px}

.news{left:674px;top:489px;width:249px;height:188px;padding:8px 12px}
.news .rule{margin:6px 0 10px}
.event{display:flex;gap:10px;padding-bottom:10px;margin-bottom:10px;border-bottom:1px dotted #2a2a8a}
.date{width:36px;text-align:center;flex:none}
.date .m{background:var(--burgundy);color:var(--white);font-size:10px;font-weight:500;padding:2px 0}
.date .d{background:#d8d8d8;color:#333;font-size:14px;font-weight:500;padding:1px 0}
.event h3{font-size:11.5px;font-weight:500;color:var(--burgundy)}
.event p{font-size:9.5px;color:#777;line-height:13px;margin-top:4px}

.card{top:697px;width:244px}
.card-photo{height:133px;background:linear-gradient(160deg,#e5e5e7,#9ca1aa)}
.card-photo.maze{background:linear-gradient(160deg,#d6d6d6,#7b7b7b)}
.card-bar{height:24px;background:var(--burgundy);display:flex;justify-content:space-between;align-items:center;color:var(--white);font-size:15px;padding-left:19px;box-shadow:0 5px 6px rgba(0,0,0,.15)}
.card-bar span.go{width:33px;height:24px;background:#5b5b5b;display:flex;align-items:center;justify-content:center}
.card-body{padding:12px 8px 0;font-size:10.5px;line-height:16px;color:#444;height:88px}
.card-body ul{list-style:none;padding-left:13px}
.card-body li::before{content:"» ";font-size:9px}
.card .more{position:static;display:block;text-align:right;padding-right:2px}

.newsletter{left:138px;top:963px;width:785px;height:36px;border:1px solid #ccc;background:#f6f6f6;display:flex;align-items:center}
.nl-tag{height:36px;width:198px;background:var(--burgundy);color:var(--white);font-size:16px;display:flex;align-items:center;gap:10px;padding-left:10px;clip-path:polygon(0 0,90% 0,100% 50%,90% 100%,0 100%);margin-left:-1px}
.nl-text{font-size:10.5px;font-weight:500;color:#333;margin-left:14px;width:340px}
.nl-field{margin-left:30px;width:162px;height:20px;background:#dcdcdc;border:1px solid #bbb;font-size:10.5px;color:#555;padding:3px 7px}
.nl-btn{margin-left:9px;background:#595959;color:var(--white);font-size:11px;font-weight:500;padding:4px 8px}

.footer{left:0;top:1017px;width:1063px;height:183px;background:var(--footer);border-top:2px solid #555;color:var(--white)}
.footer h4{font-size:13.5px;font-weight:500;padding-bottom:3px;border-bottom:1px solid #555}
.quick{left:142px;top:15px;width:88px}
.quick ul{list-style:none;margin-top:5px}
.quick li{font-size:10.5px;font-weight:500;line-height:17.5px;padding-left:2px}
.locations{left:247px;top:15px;width:178px}
.map{left:247px;top:40px;width:187px;height:116px;background:linear-gradient(#e6e4dd,#d8d6cf);border:2px solid #fff}
.contact{left:455px;top:15px;width:151px}
.contact-list{left:451px;top:46px;list-style:none}
.contact-list li{display:flex;gap:10px;font-size:11px;line-height:14px;margin-bottom:14px}
.contact-list svg{flex:none;margin-top:1px}
.follow{left:760px;top:20px;display:flex;align-items:center;gap:8px;font-size:13.5px;font-weight:500}
.follow span.s{width:23px;height:23px;background:#888;border:2px solid #bbb;border-radius:3px}
.foot-brand{left:683px;top:76px;font-size:30px;color:var(--white);letter-spacing:1px;display:flex;align-items:center;gap:9px}
.foot-brand i{width:18px;height:18px;background:var(--burgundy);display:block}
.copy{left:690px;top:133px;width:225px;text-align:center;font-size:11px;line-height:14px;font-weight:300}
</style>
</head>
<body>

<header>
  <div class="abs brand"><span class="brand-mark"></span>QRV Advisors</div>
  <div class="abs call">
    <svg width="20" height="20" viewBox="0 0 20 20"><circle cx="10" cy="10" r="9" fill="none" stroke="#a0063a" stroke-width="1.6"/><path d="M7 5c-1 1-1 3 0 5s3 4 5 5l1.5-1.5-2-2-1 1c-1-.5-2-1.5-2.5-2.5l1-1-2-2z" fill="#a0063a"/></svg>
    Call us <b>(012) 555-0147</b>
  </div>
  <nav class="abs nav">
    <a class="current" href="#">HOME</a><a href="#">ABOUT US</a><a href="#">BUYER SERVICES</a><a href="#">SELLER SERVICES</a><a href="#">NEWS &amp; EVENTS</a><a href="#">FAQ's</a><a href="#">CONTACT US</a>
  </nav>
</header>

<section class="abs hero">
  <div class="abs hero-photo" role="img" aria-label="Photo of advisors shaking hands with a smiling client"></div>
  <div class="abs hero-caption">QRV Services Are Offered By Industry Executives With Extensive M&amp;A Experience</div>
  <div class="abs hero-arrows">
    <span><svg width="24" height="12"><path d="M2 2l10 8 10-8" fill="none" stroke="#a0063a" stroke-width="1.8"/></svg></span>
    <span><svg width="24" height="12"><path d="M2 10l10-8 10 8" fill="none" stroke="#a0063a" stroke-width="1.8"/></svg></span>
  </div>
</section>

<section class="abs panel welcome">
  <h2>Welcome to <em>QRV Advisors</em></h2>
  <div class="rule"></div>
  <p>QRV assists business owners within the logistics industry to implement growth and exit strategies. We offer business planning and merger and acquisition(M&amp;A) advisory services. QRV services are offered by industry executives with extensive M&amp;A experience. Your company will benefit from a unique and outside perspective from consultants that understand your business.</p>
  <p>QRV can help you formulate and execute your growth strategy. We take a strategic and consultative approach with our advisory services ...</p>
  <a class="more" href="#">Read More »</a>
</section>

<section class="abs panel news">
  <h2>News/Events</h2>
  <div class="rule"></div>
  <div class="event"><div class="date"><div class="m">MAR</div><div class="d">29</div></div>
    <div><h3>Duis aute irure reprehenderit</h3><p>Lorem consectetur adipiscing elit. Morbi tristique sem.</p></div></div>
  <div class="event"><div class="date"><div class="m">APR</div><div class="d">01</div></div>
    <div><h3>Duis aute irure reprehenderit</h3><p>Lorem consectetur adipiscing elit. Morbi tristique sem.</p></div></div>
  <a class="more" href="#">Read More »</a>
</section>

<article class="abs card" style="left:142px">
  <div class="card-photo" role="img" aria-label="Photo of a business team closing a deal"></div>
  <div class="card-bar">What We Do<span class="go"><svg width="12" height="10"><path d="M1 5h8M6 1l4 4-4 4" fill="none" stroke="#fff" stroke-width="2"/></svg></span></div>
  <div class="card-body">Lorem consectetur adipiscing elit. Morbi tristique sem. Nunc nec ipsum sed nisi Morbi tristique sem.Lorem consectetur adipiscing elit consectetur adi pis cing elit.</div>
  <a class="more" href="#">Read More »</a>
</article>

<article class="abs card" style="left:406px">
  <div class="card-photo" role="img" aria-label="Photo of consultants meeting around a table"></div>
  <div class="card-bar">Our Services<span class="go"><svg width="12" height="10"><path d="M1 5h8M6 1l4 4-4 4" fill="none" stroke="#fff" stroke-width="2"/></svg></span></div>
  <div class="card-body"><ul><li>Business Analysis</li><li>Business Intelligence</li><li>Mergers</li><li>Acquisition</li></ul></div>
  <a class="more" href="#">Read More »</a>
</article>

<article class="abs card" style="left:671px">
  <div class="card-photo maze" role="img" aria-label="Illustration of a maze with a goal at its centre"></div>
  <div class="card-bar">Our Mission<span class="go"><svg width="12" height="10"><path d="M1 5h8M6 1l4 4-4 4" fill="none" stroke="#fff" stroke-width="2"/></svg></span></div>
  <div class="card-body">Lorem consectetur adipiscing elit. Morbi tristique sem. Nunc nec ipsum sed nisi Morbi tristique sem.Lorem consectetur adipiscing elit consectetur ad ipis cing elit.</div>
  <a class="more" href="#">Read More »</a>
</article>

<section class="abs newsletter">
  <div class="nl-tag"><svg width="18" height="18" viewBox="0 0 18 18"><path d="M2 3h9M2 3v13h12v-6" fill="none" stroke="#fff" stroke-width="1.6"/><path d="M7 11l8-8 2 2-8 8H7z" fill="#fff"/></svg>Newsletter Signup</div>
  <div class="nl-text">Lorem ipsum doloronsectetur adipiscing elit. Morbi id tristique.</div>
  <div class="nl-field">Email address</div>
  <div class="nl-btn">SUBMIT</div>
</section>

<footer class="abs footer">
  <div class="abs quick"><h4>Quick Link</h4>
    <ul><li>Home</li><li>About Us</li><li>Buyer Services</li><li>Seller Services</li><li>News &amp; Events</li><li>FAQ's</li><li>Contact us</li></ul></div>
  <div class="abs locations"><h4>QRV Locations</h4></div>
  <div class="abs map" role="img" aria-label="Street map showing the office location"></div>
  <div class="abs contact"><h4>Contact Us</h4></div>
  <ul class="abs contact-list">
    <li><svg width="16" height="14"><path d="M1 7l7-6 7 6M3 6v7h10V6" fill="none" stroke="#a0063a" stroke-width="1.6"/></svg>Lorem consectetur adipiscing<br>elit. Morbi tristique sem.</li>
    <li><svg width="16" height="14"><circle cx="8" cy="7" r="6" fill="none" stroke="#a0063a" stroke-width="1.4"/><path d="M6 4c-1 1 0 4 3 6l1-1-1.5-1.5-.7.7C7 7.5 6.5 7 6.2 6.3l.7-.7L5.5 4z" fill="#a0063a"/></svg>(012) 555-0147</li>
    <li><svg width="16" height="14"><rect x="1" y="5" width="14" height="8" fill="#a0063a"/><rect x="4" y="1" width="8" height="4" fill="none" stroke="#a0063a" stroke-width="1.4"/></svg>(012) 555-0147</li>
    <li><svg width="16" height="14"><rect x="1" y="3" width="14" height="9" fill="#a0063a"/><path d="M1 3l7 5 7-5" fill="none" stroke="#0d0d0d" stroke-width="1.2"/></svg>hello@qrvadvisors-example.com</li>
  </ul>
  <div class="abs follow">Follow Us:<span class="s"></span><span class="s"></span><span class="s"></span></div>
  <div class="abs foot-brand"><i></i>QRV Advisors</div>
  <div class="abs copy">© 2014 QRV ADVISORS.<br>All rights reserved.</div>
</footer>

</body>
</html>
```